Redesign of business card for Cedar Ridge Mechanical

We are looking for a new design for our business cards for Cedar Ridge Mechanical. We are a plumbing & HVAC construction company, operating on the West Coast of Canada and USA. Logo attached.
Industry/Entity Type
Construction - Plumbing & HVAC
Contact Information for Business Card
Name, address, phone numbers, email, website address
Look and feel
Each slider illustrates characteristics of the customer's brand and the style your logo design should communicate.

```html
<!DOCTYPE html>
<html lang="en">
<head>
<meta charset="utf-8">
<title>Cedar Ridge Mechanical – Business Card</title>
<link href="https://fonts.googleapis.com/css2?family=Montserrat:wght@300;400;700&display=swap" rel="stylesheet">
<style>
  :root {
    --backdrop: #6b6b6b;
    --card-white: #ffffff;
    --card-black: #141414;
    --ink: #1a1a1a;
    --ink-soft: #6e6e6e;
    --rule: #4a4a4a;
    --reverse: #ffffff;
  }
  * { margin: 0; padding: 0; box-sizing: border-box; }
  html, body {
    width: 1200px; height: 800px; overflow: hidden;
    background: var(--backdrop);
    font-family: "Montserrat", sans-serif;
  }
  .canvas {
    position: relative; width: 1200px; height: 800px;
    display: flex; align-items: center; justify-content: center; gap: 40px;
  }
  .card {
    position: relative; width: 540px; height: 309px;
    border-radius: 22px; overflow: hidden;
    box-shadow: 0 10px 24px rgba(0,0,0,0.35);
  }
  .card--front { background: var(--card-white); color: var(--ink); }
  .card--back { background: var(--card-black); }

  .brand {
    position: absolute; display: flex; align-items: center; gap: 12px;
    font-weight: 700; text-transform: uppercase; line-height: 1.15;
  }
  .brand__mark { flex: none; width: 40px; height: 40px; border: 5px solid currentColor; border-radius: 6px; }
  .card--front .brand { left: 34px; top: 50%; transform: translateY(-50%); font-size: 17px; letter-spacing: 0.04em; color: var(--ink); }
  .card--back .brand { right: 60px; bottom: 70px; font-size: 13px; letter-spacing: 0.05em; color: var(--reverse); }
  .card--back .brand__mark { width: 30px; height: 30px; border-width: 4px; }

  .divider {
    position: absolute; left: 262px; top: 36px; bottom: 36px;
    width: 1px; background: var(--rule);
  }
  .details { position: absolute; left: 286px; top: 40px; right: 18px; }
  .details__name { font-size: 19px; font-weight: 700; letter-spacing: 0.02em; text-transform: uppercase; }
  .details__title { font-size: 13px; font-weight: 300; color: var(--ink-soft); margin-top: 2px; }
  .details__address { font-size: 12px; font-weight: 300; color: var(--ink-soft); margin-top: 20px; line-height: 1.55; }
  .contact { list-style: none; margin-top: 18px; }
  .contact__item {
    display: flex; align-items: center; gap: 8px;
    font-size: 12px; font-weight: 300; color: var(--ink-soft); line-height: 1.9;
  }
  .contact__icon { width: 11px; height: 11px; flex: none; fill: var(--ink); }
</style>
</head>
<body>
<main class="canvas">
  <section class="card card--front" aria-label="Business card front">
    <div class="brand"><span class="brand__mark"></span><span>Cedar Ridge<br>Mechanical</span></div>
    <div class="divider"></div>
    <div class="details">
      <h1 class="details__name">Marcus Tolland</h1>
      <p class="details__title">President</p>
      <p class="details__address">4170 Harbor View Road<br>Suite 200, Tacoma, WA 98402</p>
      <ul class="contact">
        <li class="contact__item">
          <svg class="contact__icon" viewBox="0 0 16 16"><path d="M3.6 1l2.6 3-1.5 1.8c.9 2 2.5 3.6 4.5 4.5l1.8-1.5 3 2.6-1.6 2.6C7.2 14 2 8.8 1 3.2z"/></svg>
          1-866-555-0142 Toll Free
        </li>
        <li class="contact__item">
          <svg class="contact__icon" viewBox="0 0 16 16"><path d="M3.6 1l2.6 3-1.5 1.8c.9 2 2.5 3.6 4.5 4.5l1.8-1.5 3 2.6-1.6 2.6C7.2 14 2 8.8 1 3.2z"/></svg>
          253-555-0187
        </li>
        <li class="contact__item">
          <svg class="contact__icon" viewBox="0 0 16 16"><path d="M1 3h14v10H1z M1 3l7 6 7-6" fill="var(--ink)"/><path d="M1.5 3.5l6.5 5.5 6.5-5.5" fill="none" stroke="#fff" stroke-width="1.2"/></svg>
          info@cedarridgemech.com
        </li>
        <li class="contact__item">
          <svg class="contact__icon" viewBox="0 0 16 16"><circle cx="8" cy="8" r="7"/><path d="M1 8h14M8 1c-3 3.5-3 10.5 0 14M8 1c3 3.5 3 10.5 0 14" fill="none" stroke="#fff" stroke-width="1"/></svg>
          www.cedarridgemech.com
        </li>
      </ul>
    </div>
  </section>

  <section class="card card--back" aria-label="Business card back">
    <div class="brand"><span class="brand__mark"></span><span>Cedar Ridge<br>Mechanical</span></div>
  </section>
</main>
</body>
</html>
```